Letterhead and matching envelope design for a dental office

We need a new stationary design, letterhead and envelope #10, for a dental office in Denver area. We are called Bright Harbor Dental. We want a simple and minimalistic design but not a boring design. I wish to have one good point that makes it look professional. I have attached our logo. Feel free to use either one. I want the design for letterhead and envelope look like a "matching pair" but not look the same. The envelope doesn't have to be white and it will have an address window on bottom left.

Target Market(s)

everyone who visits dentist (adults)

Industry/Entity Type

Dental

Font styles to use
Other font styles liked:
• close to font on logo or something that matches well

Requirements
Must have
• professional
• simple, minimalistic
• unique point that stands out
Nice to have
• matching but not same design for letterhead and envelope
Should not have
• not look like all the other boring designs
• no flowery, distracting feats

```html
<!DOCTYPE html>
<html lang="en">
<head>
<meta charset="utf-8">
<title>Bright Harbor Dental – Envelope #10 Stationery</title>
<link rel="stylesheet" href="https://fonts.googleapis.com/css2?family=PT+Sans:wght@400;700&display=swap">
<style>
  :root {
    --brand-green: #3bb54a;
    --brand-green-soft: #a9dbae;
    --leaf-tint: #eef6ec;
    --text-dark: #2d2d2d;
    --paper: #ffffff;
    --backdrop: #e4e4e4;
    --fold-line: #ececec;
    --window-line: #dcdcdc;
  }
  * { box-sizing: border-box; margin: 0; padding: 0; }
  html, body { width: 1200px; height: 795px; overflow: hidden; }
  body {
    background: var(--backdrop);
    font-family: "PT Sans", Arial, sans-serif;
    position: relative;
  }
  .envelope {
    position: absolute;
    width: 700px;
    height: 304px;
    background: var(--paper);
    overflow: hidden;
  }
  .envelope--back { left: 420px; top: 48px; }
  .envelope--front { left: 80px; top: 440px; }

  .leaf-motif {
    position: absolute;
    border-radius: 60% 40% 55% 45%;
    background: radial-gradient(ellipse at 40% 50%, var(--leaf-tint) 0%, rgba(238,246,236,0.6) 70%, rgba(238,246,236,0) 100%);
  }
  .envelope--front .leaf-motif { left: 300px; top: 80px; width: 300px; height: 140px; }
  .envelope--back .leaf-motif { left: 170px; top: 120px; width: 340px; height: 140px; }

  .fold-line {
    position: absolute;
    left: 0; right: 0;
    height: 1px;
    background: var(--fold-line);
  }
  .fold-line--upper { top: 72px; }
  .fold-line--lower { top: 232px; }

  .brand-name {
    position: absolute;
    left: 36px; top: 28px;
    display: flex; align-items: center; gap: 8px;
    color: var(--brand-green);
    font-size: 15px;
    font-weight: 700;
    letter-spacing: 2px;
    text-transform: uppercase;
  }
  .brand-name .brand-dot {
    width: 12px; height: 12px; border-radius: 50%;
    background: var(--brand-green);
  }

  .address-window {
    position: absolute;
    left: 36px; top: 112px;
    width: 250px; height: 96px;
    border: 1px solid var(--window-line);
    border-radius: 6px;
  }

  .website {
    position: absolute;
    left: 38px;
    color: var(--brand-green);
    font-size: 13px;
    letter-spacing: 2.4px;
  }
  .envelope--front .website { top: 250px; }
  .envelope--back .website { top: 236px; }

  .return-address {
    position: absolute;
    right: 46px; top: 108px;
    text-align: right;
    font-size: 13px;
    font-style: normal;
    line-height: 1.38;
    color: var(--text-dark);
  }
  .return-address .company { color: var(--brand-green); }
  .contact-line { display: flex; justify-content: flex-end; align-items: center; gap: 5px; }
  .contact-icon {
    width: 13px; height: 13px; border-radius: 50%;
    background: var(--brand-green);
    display: inline-flex; align-items: center; justify-content: center;
  }
  .edge-bar { position: absolute; right: 0; width: 7px; }
  .edge-bar--strong { top: 108px; height: 104px; background: var(--brand-green); }
  .edge-bar--soft { top: 216px; bottom: 0; background: var(--brand-green-soft); }

  .flap { position: absolute; inset: 0; }
  .flap-mark {
    position: absolute;
    left: 468px; top: 58px;
    display: flex; align-items: center; gap: 8px;
    color: var(--paper);
    font-size: 13px;
    font-weight: 700;
    letter-spacing: 2px;
    text-transform: uppercase;
    white-space: nowrap;
  }
  .flap-mark .brand-dot {
    width: 11px; height: 11px; border-radius: 50%;
    border: 1.5px solid var(--paper);
  }
</style>
</head>
<body>

  <section class="envelope envelope--back" aria-label="Envelope back with flap">
    <div class="leaf-motif" role="img" aria-label="Faint pale green brand motif"></div>
    <svg class="flap" width="700" height="304" viewBox="0 0 700 304" aria-hidden="true">
      <path d="M0 0 H700 V232 C700 252 682 252 660 242 C520 170 330 95 70 48 C30 40 4 26 0 0 Z" fill="var(--brand-green)"/>
    </svg>
    <div class="flap-mark"><span class="brand-dot"></span>Bright Harbor Dental</div>
    <p class="website">www.brightharbordental.com</p>
  </section>

  <section class="envelope envelope--front" aria-label="Envelope front">
    <div class="leaf-motif" role="img" aria-label="Faint pale green brand motif"></div>
    <div class="fold-line fold-line--upper"></div>
    <div class="fold-line fold-line--lower"></div>

    <div class="brand-name"><span class="brand-dot"></span>Bright Harbor Dental</div>

    <div class="address-window" aria-label="Address window"></div>

    <address class="return-address">
      <div class="company">Bright Harbor Dental</div>
      <div>2871 Lantern Ridge Dr.</div>
      <div>Suite 210 Lakewood, CO 80227</div>
      <div class="contact-line">303-555-0148
        <span class="contact-icon">
          <svg width="8" height="8" viewBox="0 0 24 24" aria-hidden="true"><path fill="#fff" d="M6.6 10.8a15 15 0 0 0 6.6 6.6l2.2-2.2c.3-.3.7-.4 1-.2 1.1.4 2.3.6 3.6.6.6 0 1 .4 1 1V20c0 .6-.4 1-1 1A17 17 0 0 1 3 4c0-.6.4-1 1-1h3.5c.6 0 1 .4 1 1 0 1.3.2 2.5.6 3.6.1.3 0 .7-.2 1z"/></svg>
        </span>
      </div>
      <div class="contact-line">hello@brightharbordental.com
        <span class="contact-icon">
          <svg width="8" height="8" viewBox="0 0 24 24" aria-hidden="true"><path fill="#fff" d="M2 5h20v14H2z M4 7v.5l8 5 8-5V7l-8 5z"/></svg>
        </span>
      </div>
    </address>

    <div class="edge-bar edge-bar--strong"></div>
    <div class="edge-bar edge-bar--soft"></div>

    <p class="website">www.brightharbordental.com</p>
  </section>

</body>
</html>
```